Logo and Card design for KRV Home Solutions LLC

I need an edgier logo and business card designs. Current logo attached. I like the colors below. I would like the logo to incorporate a home in the design.
Title = Principal-Acquisitions
Email:KRVHOMESOLUTIONS@fernmail.example
555-214-0937
facebook
IG
2 sided business card with the front being contact info a slogan about selling a home fast. The back incorporating What we do. Buy houses, land, or commercial property as is. We find solutions to make the process of selling simple and fair.

Target Market(s)

Motivated house sellers.

Industry/Entity Type

Business

Contact Information for Business Card

Who we are: We are a Faith based Real Estate Investment Company. We pay cash for homes in any condition and can close quick. Whatever the reason you need to sell fast, we can help. We believe in creating win-win solutions to help you in your time of need. We care! We can help!

Logo Text

KRV Home Solutions LLC

Font styles to use
Sans Serif

Colors
33a6d7
0355a3
85abd2
cee9f5
9d9d9d
b2b2b2
ffffff

Requirements
Must have
• Old logo attached. I want something edgier.
• Company name, phone number, description on the back of what we can do. Pay all cash. Buy in as is condition. No fees,Commisions or closing costs.Close quick. No hassles with solutions to meet your unique situation.
• Call today for an offer within 24 hours.

```html
<!DOCTYPE html>
<html lang="en">
<head>
<meta charset="utf-8">
<title>KRV Home Solutions – Business Card</title>
<link rel="stylesheet" href="https://fonts.googleapis.com/css2?family=Montserrat:wght@600;700&family=Work+Sans:wght@400;500&display=swap">
<style>
  :root {
    --navy: #233a78;
    --ink: #1d2d5c;
    --grey: #5f5f63;
    --grey-light: #9d9d9d;
    --white: #ffffff;
    --backdrop: #d9d9d9;
  }
  * { box-sizing: border-box; margin: 0; padding: 0; }
  html, body { width: 1200px; height: 900px; overflow: hidden; }
  body {
    background: var(--backdrop);
    font-family: "Work Sans", sans-serif;
    display: flex;
    flex-direction: column;
    align-items: center;
    justify-content: center;
    gap: 36px;
  }
  .card {
    position: relative;
    width: 700px;
    height: 400px;
    overflow: hidden;
    box-shadow: 0 10px 24px rgba(0,0,0,.25);
  }

  /* Back side */
  .card--back {
    background: var(--navy);
    color: var(--white);
    display: flex;
    flex-direction: column;
    align-items: center;
    justify-content: center;
    text-align: center;
    gap: 46px;
  }
  .wordmark {
    font-family: "Montserrat", sans-serif;
    font-weight: 700;
    line-height: 1.05;
    text-align: center;
  }
  .wordmark__main { display: block; font-size: 40px; letter-spacing: 1px; }
  .wordmark__sub { display: block; font-size: 18px; letter-spacing: 2px; }
  .card--back .wordmark { color: var(--white); }
  .services {
    font-size: 16px;
    line-height: 1.45;
    letter-spacing: .3px;
    max-width: 560px;
  }

  /* Front side */
  .card--front { background: var(--white); }
  .card--front .wordmark {
    position: absolute;
    top: 62px;
    right: 40px;
    color: var(--navy);
  }
  .card--front .wordmark__main { font-size: 34px; }
  .card--front .wordmark__sub { font-size: 16px; }
  .identity {
    position: absolute;
    left: 60px;
    top: 150px;
    right: 40px;
  }
  .company-name {
    font-family: "Montserrat", sans-serif;
    font-weight: 700;
    font-size: 30px;
    color: var(--navy);
    letter-spacing: .5px;
  }
  .title-row {
    display: flex;
    align-items: center;
    gap: 10px;
    margin-top: 2px;
  }
  .job-title {
    font-size: 16px;
    color: var(--grey);
    white-space: nowrap;
  }
  .title-rule {
    flex: 1;
    height: 2px;
    background: var(--navy);
    margin-top: 8px;
  }
  .contacts {
    position: absolute;
    left: 60px;
    top: 222px;
    list-style: none;
    font-size: 17px;
    color: var(--grey);
    line-height: 1.35;
  }
  .contacts li { display: flex; align-items: center; gap: 10px; }
  .contacts svg { width: 14px; height: 14px; flex: none; }
  .slogan {
    position: absolute;
    right: 48px;
    bottom: 48px;
    font-family: "Montserrat", sans-serif;
    font-weight: 600;
    font-size: 17px;
    letter-spacing: 4px;
    color: var(--grey);
  }
  .base-bands {
    position: absolute;
    left: 0;
    bottom: 0;
    width: 700px;
    height: 16px;
  }
</style>
</head>
<body>

  <section class="card card--back" aria-label="Business card back">
    <div class="wordmark">
      <span class="wordmark__main">KRV HOME</span>
      <span class="wordmark__sub">SOLUTIONS</span>
    </div>
    <p class="services">
      Pay all cash. Buy in as is condition. No fees,Commisions<br>
      or closing costs.Close quick. No hassles with solutions<br>
      to meet your unique situation.<br>
      Call today for an offer within 24 hours.
    </p>
  </section>

  <section class="card card--front" aria-label="Business card front">
    <div class="wordmark">
      <span class="wordmark__main">KRV HOME</span>
      <span class="wordmark__sub">SOLUTIONS</span>
    </div>

    <div class="identity">
      <h1 class="company-name">KRV HOME SOLUTIONS</h1>
      <div class="title-row">
        <span class="job-title">Principal-Acquisitions</span>
        <span class="title-rule"></span>
      </div>
    </div>

    <ul class="contacts">
      <li>
        <svg viewBox="0 0 14 14" aria-hidden="true"><circle cx="7" cy="7" r="7" fill="var(--navy)"/><path d="M4.6 3.5l1.3 1.8-.8.9c.5 1.1 1.4 2 2.6 2.6l.9-.8 1.8 1.3-.7 1.3C6.8 10.4 3.6 7.2 3.3 4.2z" fill="#fff"/></svg>
        555-214-0937
      </li>
      <li>
        <svg viewBox="0 0 14 14" aria-hidden="true"><circle cx="7" cy="7" r="7" fill="var(--navy)"/></svg>
        /krvhomesolutions
      </li>
      <li>
        <svg viewBox="0 0 14 14" aria-hidden="true"><circle cx="7" cy="7" r="7" fill="var(--navy)"/></svg>
        @krvhomesolutions
      </li>
      <li>
        <svg viewBox="0 0 14 14" aria-hidden="true"><circle cx="7" cy="7" r="7" fill="var(--navy)"/><rect x="3.5" y="4.5" width="7" height="5" fill="none" stroke="#fff" stroke-width="1"/><path d="M3.5 4.5L7 7.3l3.5-2.8" fill="none" stroke="#fff" stroke-width="1"/></svg>
        KRVHOMESOLUTIONS@fernmail.example
      </li>
    </ul>

    <p class="slogan">SELLING A HOME FAST</p>

    <svg class="base-bands" viewBox="0 0 700 16" preserveAspectRatio="none" aria-hidden="true">
      <polygon points="0,6 345,6 330,16 0,16" fill="var(--navy)"/>
      <polygon points="352,6 700,6 700,16 337,16" fill="var(--grey)"/>
    </svg>
  </section>

</body>
</html>
```